Prime Global Casting Agency Needs creative business card design

We manage actors careers and book them liaising and promoting their profiles internationally through Casting Directors, Producers, Directors, Publicists etc. We need clearly visable contact details but with a design that reflects our status and creativity of TV, Feature Film industry. Our logo is attached and needs to relate and our website is www.brisklanestagefolk.com
No flame designs please but please incorporate logo colours.

Target Market(s)

Clients

Industry/Entity Type

Film Production

Contact Information for Business Card

Director Danielle Prowse
Suite F, Building 4, Wrenlow Studios Australia, Kelby Vale, Sydney, NSW 2048

Font styles to use
Sans Serif

Colors
ec1f27

Requirements
Nice to have
• Colours should relate to logo attached and type can relate again to type in the logo design.
Should not have
• No Flames designs and best to be not too obvious with the film designs eiither. Needs to be more creative and modern

```html
<!DOCTYPE html>
<html lang="en">
<head>
<meta charset="utf-8">
<title>Brisklane Stagefolk – Business Card</title>
<link rel="stylesheet" href="https://fonts.googleapis.com/css2?family=Source+Sans+3:wght@400;600&display=swap">
<style>
  :root {
    --stage-top: #2a2a2a;
    --stage-bottom: #050505;
    --card-white: #ffffff;
    --brand-red: #d42628;
    --text-red: #d8232a;
    --text-grey: #3c3c3c;
    --mark-silver: #d6d6d6;
  }
  * { box-sizing: border-box; margin: 0; padding: 0; }
  html, body { width: 1200px; height: 900px; overflow: hidden; }
  body {
    position: relative;
    background: linear-gradient(180deg, var(--stage-top) 0%, #1a1a1a 55%, var(--stage-bottom) 100%);
    font-family: "Source Sans 3", "Myriad Pro", Arial, sans-serif;
  }
  .card {
    position: absolute;
    top: 312px;
    width: 428px;
    height: 247px;
    border-radius: 12px;
  }
  .card--front { left: 148px; background: var(--card-white); }
  .card--back { left: 633px; background: var(--brand-red); }

  .brand-name {
    position: absolute;
    display: flex;
    align-items: center;
    gap: 8px;
    font-weight: 600;
    white-space: nowrap;
  }
  .brand-name__dot { display: block; flex: none; }
  .card--front .brand-name {
    left: 34px; top: 122px;
    font-size: 17px;
    color: var(--text-red);
  }
  .card--front .brand-name__dot { width: 10px; height: 10px; background: var(--text-red); }
  .card--back .brand-name {
    left: 0; right: 0; top: 98px;
    justify-content: center;
    font-size: 34px;
    color: var(--mark-silver);
    letter-spacing: 1px;
  }
  .card--back .brand-name__dot { width: 14px; height: 14px; background: var(--mark-silver); }

  .contact {
    position: absolute;
    left: 207px; top: 46px;
    color: var(--text-grey);
    font-size: 13px;
    line-height: 15px;
  }
  .contact__name {
    font-size: 19.5px;
    line-height: 22px;
    font-weight: 600;
    color: var(--text-red);
  }
  .contact__role { margin-top: 0; }
  .contact__address { margin-top: 11px; }
  .contact__list { list-style: none; margin-top: 14px; }
  .contact__list li {
    display: flex;
    align-items: center;
    height: 16px;
  }
  .contact__icon {
    width: 9px; height: 9px;
    margin: 0 8px 0 1px;
    fill: var(--text-red);
    stroke: var(--text-red);
    flex: none;
  }
</style>
</head>
<body>
  <section class="card card--front" aria-label="Card front">
    <div class="brand-name">
      <span class="brand-name__dot"></span>Brisklane Stagefolk
    </div>

    <div class="contact">
      <p class="contact__name">Jonathan Smith</p>
      <p class="contact__role">Managing Director</p>
      <p class="contact__address">1234, Address Goes Here<br>Country Name, 123456</p>
      <ul class="contact__list">
        <li>
          <svg class="contact__icon" viewBox="0 0 10 10"><rect x="2.5" y="0.5" width="5" height="9" rx="1" fill="none" stroke-width="1.2"/><circle cx="5" cy="8" r="0.6" stroke="none"/></svg>
          123-456-7890
        </li>
        <li>
          <svg class="contact__icon" viewBox="0 0 10 10"><path d="M0.5 3.5 Q5 0.5 9.5 3.5 L8 5 L6.5 4 L3.5 4 L2 5 Z" stroke="none"/><rect x="2" y="5.5" width="6" height="3.5" rx="0.5" stroke="none"/></svg>
          123-456-7890
        </li>
        <li>
          <svg class="contact__icon" viewBox="0 0 10 10"><rect x="0.5" y="3.5" width="9" height="6" rx="0.8" stroke="none"/><rect x="2.5" y="0.5" width="5" height="3.5" fill="none" stroke-width="1"/><rect x="3" y="5.5" width="4" height="1" fill="#fff" stroke="none"/></svg>
          123-456-7890
        </li>
        <li>
          <svg class="contact__icon" viewBox="0 0 10 10"><rect x="0.5" y="2" width="9" height="6.5" stroke="none"/><path d="M0.8 2.4 L5 5.6 L9.2 2.4" fill="none" stroke="#fff" stroke-width="0.9"/></svg>
          info@youremail.com
        </li>
        <li>
          <svg class="contact__icon" viewBox="0 0 10 10"><g fill="none" stroke-width="1.3"><rect x="0.8" y="4.3" width="5" height="2.6" rx="1.3" transform="rotate(-45 3.3 5.6)"/><rect x="4.2" y="3.1" width="5" height="2.6" rx="1.3" transform="rotate(-45 6.7 4.4)"/></g></svg>
          www.yourweb.com
        </li>
      </ul>
    </div>
  </section>

  <section class="card card--back" aria-label="Card back">
    <div class="brand-name">
      <span class="brand-name__dot"></span>Brisklane Stagefolk
    </div>
  </section>
</body>
</html>
```